card for handyman and landscaping business, double sided with services listed on the back

Design a business card for a handyman and Landscaping business in San Jose,ca. Would like front to be a house with 3D characters doing different tasks i.e. Mowing lawn, painting, sprinklers, lighting, weed whacking, power washing, lumber etc. on the backside a cutout of the interior with computer, internet, cleaning, bathroom/kitchen remodeling, smart home etc.

Industry/Entity Type

Handyman

Contact Information for Business Card

Two sided view of a house, one outside services and one inside services

Colors

Designer to choose colors to be used in the design.

Requirements
Must have
• General Household Repairs and Maintenance
• Landscaping, Gardening, and Planting
• Painting, Patching and Trim/Moulding Work
• Cleaning, Restoring and Hauling/Trash Removal
• Blinds, Curtains, and Assembly Work
• Computer, Internet/Wireless, and Smart Home Service

```html
<!DOCTYPE html>
<html lang="en">
<head>
<meta charset="utf-8">
<title>Harlow Home and Yard Service – Business Card</title>
<link rel="stylesheet" href="https://fonts.googleapis.com/css2?family=Raleway:wght@700&family=Source+Sans+3:wght@400;600&display=swap">
<style>
  :root {
    --backdrop: #505050;
    --green-bright: #2e9b48;
    --green-deep: #0d4b29;
    --paper: #efefef;
    --white: #ffffff;
  }
  * { box-sizing: border-box; margin: 0; padding: 0; }
  html, body { width: 1200px; height: 900px; overflow: hidden; }
  body { background: var(--backdrop); position: relative; font-family: "Source Sans 3", "Myriad Pro", sans-serif; }

  .card { position: absolute; top: 306px; width: 440px; height: 271px; overflow: hidden; box-shadow: 0 2px 4px rgba(0,0,0,0.35); }
  .card--front { left: 149px; }
  .card--back { left: 608px; }

  .card__shapes { position: absolute; inset: 0; }

  .card__title {
    position: absolute; left: 0; right: 0; top: 3px; height: 49px;
    display: flex; align-items: center; justify-content: center;
    font-family: "Raleway", "Montserrat", sans-serif; font-weight: 700;
    font-size: 16.5px; color: var(--white); letter-spacing: 0.1px;
  }

  .contact { position: absolute; left: 30px; top: 88px; list-style: none; color: var(--white); font-size: 12.8px; }
  .contact li { display: flex; align-items: center; height: 16px; }
  .contact svg { width: 9px; height: 9px; margin-right: 5px; fill: var(--white); flex: none; }
  .contact .contact__area { margin-top: 12px; font-size: 13px; }
  .contact .contact__area svg { width: 9px; height: 12px; }

  .owner { position: absolute; right: 40px; top: 76px; color: var(--white); font-weight: 600; font-size: 16.5px; letter-spacing: 0.2px; }

  .services { position: absolute; left: 26px; top: 77px; list-style: none; color: var(--white); font-size: 11.6px; line-height: 14px; }
  .services li::before { content: "•"; display: inline-block; width: 9px; }

  .icons { position: absolute; left: 31px; top: 204px; display: flex; gap: 16px; }
  .icon { width: 50px; height: 50px; border-radius: 50%; background: var(--green-bright); display: flex; align-items: center; justify-content: center; }
  .icon svg { width: 30px; height: 30px; fill: var(--white); stroke: var(--white); }
</style>
</head>
<body>

<section class="card card--front" aria-label="Business card front">
  <svg class="card__shapes" viewBox="0 0 440 271" aria-hidden="true">
    <rect width="440" height="271" fill="var(--paper)"/>
    <rect width="440" height="49" fill="var(--green-bright)"/>
    <path d="M0 49H440V188H410V156L353 131L296 156V186H0Z" fill="var(--green-bright)"/>
    <path d="M0 49H440V184H407V154L353 129L299 154V182H0Z" fill="var(--green-deep)"/>
    <path d="M296 157L353 132L410 157V271H296Z" fill="var(--paper)"/>
  </svg>
  <h1 class="card__title">HARLOW HOME AND YARD SERVICE</h1>
  <ul class="contact">
    <li><svg viewBox="0 0 10 10"><path d="M2 0L4 2.5 3 3.6Q4.3 6 6.4 7L7.5 6 10 8 8.5 10Q2 9 0 1.5Z"/></svg>408-555-0142</li>
    <li><svg viewBox="0 0 10 10"><path d="M0 2H10V8H0Z M0.5 2.3L5 5.5 9.5 2.3" stroke="var(--green-deep)" stroke-width="0.8"/></svg>info@harlowhomeandyard.com</li>
    <li><svg viewBox="0 0 10 10"><circle cx="5" cy="5" r="5"/><path d="M2.5 3.5Q5 2 7 4L5 6 6 8Q3 8 2.5 5.5Z" fill="var(--green-deep)"/></svg>www.harlowhomeandyard.com</li>
    <li class="contact__area"><svg viewBox="0 0 10 14"><path d="M5 0A5 5 0 0 1 10 5C10 8 5 14 5 14S0 8 0 5A5 5 0 0 1 5 0Z"/><circle cx="5" cy="5" r="2" fill="var(--green-deep)"/></svg>Lakeview and Pine Ridge County</li>
  </ul>
  <p class="owner">OWEN HARLOW</p>
  <div class="icons">
    <div class="icon" aria-label="Bathroom repair"><svg viewBox="0 0 30 30"><rect x="7" y="3" width="16" height="8" rx="1" stroke="none"/><path d="M6 13H24Q24 21 17 22V27H12V22Q6 20 6 13Z" stroke="none"/></svg></div>
    <div class="icon" aria-label="Cleaning"><svg viewBox="0 0 30 30"><path d="M22 3L14 16" fill="none" stroke-width="2"/><path d="M11 15L18 19 14 27Q8 27 5 22Z" stroke="none"/></svg></div>
    <div class="icon" aria-label="Internet router"><svg viewBox="0 0 30 30"><rect x="5" y="6" width="20" height="18" rx="2" stroke="none"/><path d="M11 12Q15 9 19 12M13 14Q15 12.5 17 14" fill="none" stroke="var(--green-bright)" stroke-width="1.4"/><rect x="8" y="19" width="14" height="2" fill="var(--green-bright)" stroke="none"/></svg></div>
    <div class="icon" aria-label="Wireless"><svg viewBox="0 0 30 30" fill="none" stroke-width="1.6"><path d="M9 8Q5 13 9 18M21 8Q25 13 21 18M11.5 10.5Q9.5 13 11.5 15.5M18.5 10.5Q20.5 13 18.5 15.5"/><path d="M15 13L11 26M15 13L19 26M12.5 21H17.5"/><circle cx="15" cy="13" r="1.5" fill="var(--white)"/></svg></div>
    <div class="icon" aria-label="Lighting"><svg viewBox="0 0 30 30"><circle cx="15" cy="14" r="6" stroke="none"/><rect x="12" y="19" width="6" height="5" stroke="none"/><path d="M15 3V5M6 14H8M22 14H24M8.5 7.5L10 9M21.5 7.5L20 9" stroke-width="1.5"/></svg></div>
    <div class="icon" aria-label="Smart home"><svg viewBox="0 0 30 30"><path d="M15 3L27 14H24V26H6V14H3Z" stroke="none"/><circle cx="15" cy="17" r="4.5" fill="none" stroke="var(--green-bright)" stroke-width="1.5"/><path d="M15 11V16" stroke="var(--green-bright)" stroke-width="1.5"/></svg></div>
  </div>
</section>

<section class="card card--back" aria-label="Business card back">
  <svg class="card__shapes" viewBox="0 0 440 271" aria-hidden="true">
    <rect width="440" height="271" fill="var(--paper)"/>
    <rect width="440" height="49" fill="var(--green-bright)"/>
    <path d="M0 49H440V190H425V156L368 131L308 156V188H0Z" fill="var(--green-bright)"/>
    <path d="M0 49H440V186H422V154L368 129L311 154V184H0Z" fill="var(--green-deep)"/>
    <path d="M308 157L368 132L425 157V271H308Z" fill="var(--paper)"/>
  </svg>
  <h2 class="card__title">HANDYMAN&nbsp; LANDSCAPING &amp; TECH SERVICES</h2>
  <ul class="services">
    <li>General Household Repairs and Maintenance</li>
    <li>Landscaping, Gardening, and Planting</li>
    <li>Painting, Patching and Trim/Moulding Work</li>
    <li>Cleaning, Restoring and Hauling/Trash Removal</li>
    <li>Blinds, Curtains, and Assembly Work</li>
    <li>Computer, Internet/Wireless, and Smart Home Service</li>
  </ul>
  <div class="icons">
    <div class="icon" aria-label="Lawn mowing"><svg viewBox="0 0 30 30"><path d="M3 8L12 17" fill="none" stroke-width="1.8"/><path d="M10 16H24L27 22H10Z" stroke="none"/><circle cx="13" cy="23" r="3" stroke="var(--green-bright)"/><circle cx="24" cy="23" r="3" stroke="var(--green-bright)"/></svg></div>
    <div class="icon" aria-label="Trim work"><svg viewBox="0 0 30 30"><path d="M8 4L14 3 16 14 11 15Z" stroke="none"/><path d="M12 15L14 23" stroke-width="2"/><rect x="3" y="22" width="24" height="4" stroke="none"/></svg></div>
    <div class="icon" aria-label="Painting"><svg viewBox="0 0 30 30"><rect x="6" y="4" width="17" height="7" rx="1.5" stroke="none"/><path d="M23 7.5H26V14H15V18" fill="none" stroke-width="1.6"/><rect x="13" y="18" width="4" height="9" rx="1" stroke="none"/></svg></div>
    <div class="icon" aria-label="Power washing"><svg viewBox="0 0 30 30"><path d="M3 11H19V15H10L9 24H5L6 15H3Z" stroke="none"/><path d="M19 13H23M24 10L28 8M24 13H28M24 16L28 18" fill="none" stroke-width="1.2"/></svg></div>
    <div class="icon" aria-label="Trash hauling"><svg viewBox="0 0 30 30"><path d="M8 5H22V8H8Z M8 9H22L20 26H10Z" stroke="none"/><circle cx="11" cy="25" r="2.5" stroke="var(--green-bright)"/></svg></div>
    <div class="icon" aria-label="Windows and blinds"><svg viewBox="0 0 30 30"><rect x="4" y="4" width="22" height="22" stroke="none"/><path d="M7 7H13.5V13.5H7Z M16.5 7H23V13.5H16.5Z M7 16.5H13.5V23H7Z M16.5 16.5H23V23H16.5Z" fill="var(--green-bright)" stroke="none"/></svg></div>
  </div>
</section>

</body>
</html>
```